Financial investment calculator report for real estae - layout & design

I am looking to Create a web report utilizing the attached information. It is an investment calculator report that will be customized report based on an online calculator. Therefore the report will need to be designed in a manner that a backend developer will be able to build off of.

The report will need to be web based but also printed in PDF format. The report will need to include the calculation format as well as be templeted to add a report user unique profile information like Headshot, Business Logo, Name, Telephone number, email etc.

The report should be modern and clean and easy to read and use a modern clean template design. It should be able to be easily color customized by the end user to produce templets in Red, Blue, Green, and Greyscale.

The report should be no more than 3 pages total with out breaking up the sections.

Section One - Cover sheet including agent bio info, Report Title and property address (both prominent), 400 Character space for property description, Property Pictures (3), and a google Maps integration image showing property location, It should also have room for about 100 words for a text disclaimer. (I will provide text soon)

Section Two - Inputs from the calculator

Section 3 - The Four Benefits & Rates of Return

Once I have a completed/approved form I will have about a half dozen forms/reports that will need to be laid out with a similar aesthetic.

Feel free to ask me any questions. Thank You
Milo

Target Market(s)

This report will be produced by real estate agents forvtheir investor clients. It should denote professionalism

Font styles to use
Sans Serif

Colors
0054AA
0677BA
7BADD7
CADEEF
E8F1F8
00AB8E
00BBA5
67D7C9
C6EFE9
E9F9F6
EB3D1F
EC4F4E
F09395
F8D3D4
FCEDEE

```html
<!DOCTYPE html>
<html lang="en">
<head>
<meta charset="utf-8">
<title>Investment Analysis – 418 Harlow</title>
<link rel="stylesheet" href="https://fonts.googleapis.com/css2?family=Lato:wght@300;400;700&display=swap">
<style>
:root{
  --accent:#2a0ff0;
  --ink:#111;
  --text:#444;
  --muted:#666;
  --rule:#dcdcdc;
  --band:#efefef;
  --card:#fafafa;
  --negative:#e53935;
  --map-fill:#e4e9f1;
  --photo:#3c4a3a;
}
*{box-sizing:border-box;margin:0;padding:0}
html,body{width:849px;height:1200px;overflow:hidden;background:#fff}
body{font-family:'Lato',sans-serif;color:var(--ink);position:relative}

.agency-mark{position:absolute;left:38px;top:42px;width:84px;height:84px;border-radius:50%;background:#000}
.agency-name{position:absolute;left:136px;top:76px;font-size:15.5px;font-weight:400;letter-spacing:.2px}
.agency-name b{font-weight:700}

.report-title{position:absolute;left:37px;top:138px;font-size:29px;font-weight:300;letter-spacing:.2px}
.report-title b{font-weight:700}
.title-rule{position:absolute;left:38px;top:179px;width:775px;height:1px;background:var(--rule)}
.title-rule::before{content:"";position:absolute;left:0;top:-1px;width:273px;height:2px;background:var(--accent)}

.agent{position:absolute;right:201px;top:28px;text-align:right}
.agent-name{font-size:15px;color:var(--accent);font-weight:400;letter-spacing:.3px}
.agent-name b{font-weight:700}
.agent-phone{font-size:11.5px;margin-top:4px;display:flex;justify-content:flex-end;align-items:center;gap:22px}
.agent-email{font-size:11.5px;margin-top:6px}
.agent-photo{position:absolute;left:661px;top:28px;width:130px;height:139px;border-radius:8px;background:linear-gradient(160deg,#8fb0b8,#4f5e4c 55%,var(--photo));box-shadow:0 2px 6px rgba(0,0,0,.18)}

.map{position:absolute;left:39px;top:200px;width:344px;height:190px;border-radius:8px;background:var(--map-fill);box-shadow:0 1px 5px rgba(0,0,0,.15)}

.property{position:absolute;left:415px;top:193px;width:392px}
.property h1{font-size:23px;font-weight:700;letter-spacing:.2px}
.property .type{font-size:10px;font-weight:700;margin-top:2px}
.property p{font-size:8px;line-height:13.5px;color:var(--text);margin-top:10px;width:392px}
.property .location{display:flex;align-items:center;gap:9px;font-size:10px;font-weight:700;margin-top:12px}
.price{display:flex;justify-content:space-between;align-items:baseline;margin-top:10px;padding:0 0 0 1px;width:375px}
.price span{font-size:11px;font-weight:700}
.price strong{font-size:15.5px;color:var(--accent)}

.card{position:absolute;left:39px;top:406px;width:774px;height:754px;background:var(--card);border-radius:9px;box-shadow:0 1px 6px rgba(0,0,0,.12);padding:11px 15px 0 15px}
.band{height:29px;background:var(--band);border-radius:5px;display:grid;grid-template-columns:333px 198px 1fr;align-items:center;font-size:11.5px;font-weight:400;text-transform:uppercase;position:relative;padding-left:30px}
.band::before{content:"";position:absolute;left:12px;top:12px;width:5px;height:5px;border-radius:50%;background:var(--accent)}
.band small{font-size:8px;text-transform:none}
.rows{margin-left:42px}
.row{display:grid;grid-template-columns:178px 142px 199px 1fr;height:20.4px;align-items:center;border-bottom:1px solid var(--rule);font-size:8.3px;color:var(--text)}
.row .v{text-align:right}
.row .split{display:flex;justify-content:space-between}
.row.last{border-bottom:none}
.neg{color:var(--negative)}
.total{display:grid;grid-template-columns:178px 142px 199px 1fr;align-items:center;height:24px;border-top:2px solid var(--accent);font-size:11.5px;font-weight:700}
.total.partial{margin-left:320px;grid-template-columns:199px 1fr}
.total .v{text-align:right}
.sub{font-size:11.5px;margin:13px 0 2px;text-transform:uppercase}
.gap{height:9px}

.footer{position:absolute;left:38px;right:36px;top:1178px;display:flex;justify-content:space-between;font-size:7.8px;color:var(--muted)}
</style>
</head>
<body>
<div class="agency-mark"></div>
<div class="agency-name"><b>AGENCYNAME</b> HERE</div>
<div class="report-title"><b>Investment</b> Analysis:</div>
<div class="title-rule"></div>

<div class="agent">
  <div class="agent-name"><b>GREG</b> MILO</div>
  <div class="agent-phone">
    <svg width="11" height="11" viewBox="0 0 24 24" fill="none" stroke="#111" stroke-width="2"><path d="M5 3h4l2 5-3 2a11 11 0 0 0 6 6l2-3 5 2v4a2 2 0 0 1-2 2A17 17 0 0 1 3 5a2 2 0 0 1 2-2z"/></svg>
    <span>(555) 014-2290</span>
  </div>
  <div class="agent-email">greg@milorealty.example</div>
</div>
<div class="agent-photo" role="img" aria-label="Agent headshot"></div>

<div class="map" role="img" aria-label="Map showing the property location in the city"></div>

<section class="property">
  <h1>418 HARLOW</h1>
  <div class="type">15-Plex of 1bd/1bth Apartments</div>
  <p>Urban bliss in this chic 400 sqft apartment. Step into a bright and open space with stylish décor. Relax on a cozy sofa or entertain in the dining area. The well-equipped kitchen features modern appliances and ample storage. Unwind in the tranquil bedroom with a queen-sized bed. Refresh in the pristine bathroom with a walk-in shower. Enjoy high-speed internet, a smart TV, and laundry facilities. Take in city views from the private balcony. Explore trendy cafes, shops, and restaurants nearby. Embrace the perfect blend of comfort and style in this urban sanctuary.</p>
  <div class="location">
    <svg width="9" height="12" viewBox="0 0 12 16"><path d="M6 0a6 6 0 0 0-6 6c0 4.5 6 10 6 10s6-5.5 6-10a6 6 0 0 0-6-6zm0 8.3A2.3 2.3 0 1 1 6 3.7a2.3 2.3 0 0 1 0 4.6z" fill="#111"/></svg>
    <span>15-Plex of 1bd/1bth Apartments</span>
  </div>
  <div class="price"><span>PURCHASE PRICE:</span><strong>$1.690.000</strong></div>
</section>

<main class="card">
  <div class="band">Property Address:</div>
  <div class="rows">
    <div class="row"><span>Financing</span><span></span><span>20% Down</span><span class="v">20 Year Conventional</span></div>
    <div class="row"><span>Purchase Price</span><span></span><span></span><span class="v">$1.690.000</span></div>
    <div class="row"><span>Down Payment (Cash Invested)</span><span></span><span>20% of purchase price</span><span class="v">$338.000</span></div>
    <div class="row"><span>Amount Financed</span><span></span><span></span><span class="v">$1.352.000</span></div>
    <div class="row"><span>Needed Capital Improvements Est</span><span></span><span></span><span class="v">$0</span></div>
    <div class="row"><span>Est. Closing Costs</span><span></span><span></span><span class="v">$3.000</span></div>
    <div class="row last"><span>CASH Invested (Down Pmt. + Closing Costs)</span><span></span><span></span><span class="v">$341.000</span></div>
    <div class="total"><span>Rate: 7%</span><span>Term: 20 years</span><span>Monthly P&amp;I:</span><span class="v">$10.482</span></div>
  </div>
  <div class="gap"></div>

  <div class="band"><span>Depriciation (First Year): (Assumes 80%/20%)</span><small>Est. Value</small><small>Yearly Rate</small></div>
  <div class="rows">
    <div class="row"><span>Land Cost</span><span>0 Year</span><span>$338.000</span><span class="split"><span>0%</span><span>$0</span></span></div>
    <div class="row"><span>Personal Property Cost</span><span>5 Years</span><span>$45.000</span><span class="split"><span>20%</span><span>$9.000</span></span></div>
    <div class="row"><span>Building Cost</span><span>27.5 Years</span><span>$1.262.000</span><span class="split"><span>3.48%</span><span>$43.918</span></span></div>
    <div class="row last"><span>Land Improvement Cost</span><span>15 Years</span><span>$45.000</span><span class="split"><span>5%</span><span>$2.250</span></span></div>
    <div class="total partial"><span>Total Depreciation:</span><span class="v">$55.168</span></div>
  </div>
  <div class="gap"></div>

  <div class="band">Income:</div>
  <div class="rows">
    <div class="row"><span>Annual Rent</span><span></span><span></span><span class="v">$170.000</span></div>
    <div class="row"><span>Other Income</span><span></span><span></span><span class="v">$0</span></div>
    <div class="row last"><span>Less Vacancy</span><span></span><span>est. 5% of annual rent</span><span class="v neg">-$0</span></div>
    <div class="total partial"><span>Gross Operating Income:</span><span class="v">$170.000</span></div>
  </div>
  <div class="gap"></div>

  <div class="band">Expenses:</div>
  <div class="rows">
    <div class="row"><span>Real Estate Tax</span><span></span><span></span><span class="v">$27.439</span></div>
    <div class="row"><span>Insurance</span><span></span><span>est.</span><span class="v">$3.492</span></div>
    <div class="row"><span>Association Dues/HOA's</span><span></span><span></span><span class="v">$0</span></div>
    <div class="row"><span>Management</span><span></span><span>0%</span><span class="v">$0</span></div>
    <div class="row"><span>Utilities</span><span></span><span></span><span class="v">$9.192</span></div>
    <div class="sub">Property Address</div>
    <div class="row"><span>Advertising</span><span></span><span></span><span class="v">$170.000</span></div>
    <div class="row"><span>Maintnence</span><span></span><span>est.</span><span class="v">$40.123</span></div>
    <div class="row"><span>Miscellaneous1</span><span></span><span>est.</span><span class="v">$129.877</span></div>
    <div class="row last"><span>Miscellaneous2</span><span></span><span>est.</span><span class="v">$125.784</span></div>
    <div class="total partial"><span>Total Expenses:</span><span class="v">$4.092</span></div>
  </div>
</main>

<footer class="footer">
  <span>418 Harlow, REF #47v8487 by Northpine Invest | Report at www.milorealty.example. June 26th, 2023</span>
  <span>Page 1/2</span>
</footer>
</body>
</html>
```